Consulting company business cards

We have a base design, but would be willing to update. We have a new logo/"tag" that needs to be added. Current business card design is attached for reference into our "style."

Industry/Entity Type

Business

Contact Information for Business Card

Should contain name and title, office number, mobile number if appropriate, e-mail, website, physical address, and company logo.

Font styles to use
Other font styles liked:
• See current card design on KorvandBCard

Colors
0455a3
85acd3
aaaaaa

Requirements
Must have
• Our colors are navy blue, gray, and a lighter blue
Nice to have
• Design that I can easily drop in new names/titles as we hire employees.

```html
<!DOCTYPE html>
<html lang="en">
<head>
<meta charset="utf-8">
<title>Tarrow Business Cards</title>
<link href="https://fonts.googleapis.com/css2?family=Lato:wght@300;400;700;900&display=swap" rel="stylesheet">
<style>
  :root{
    --navy:#12304d;
    --navy-deep:#0c2540;
    --brand-blue:#0455a3;
    --light-blue:#85acd3;
    --gray:#aaaaaa;
    --text-gray:#5f6770;
    --card-white:#f7f8f9;
    --stage:#1c1c1c;
  }
  *{box-sizing:border-box;margin:0;padding:0}
  html,body{width:1200px;height:873px;overflow:hidden;background:var(--stage)}
  body{font-family:"Lato",sans-serif;position:relative}

  .card{position:absolute;width:500px;height:286px;border-radius:14px;overflow:hidden;box-shadow:0 14px 40px rgba(0,0,0,.55)}
  .card--front{left:70px;top:293px;background:var(--card-white)}
  .card--back{left:630px;top:293px;background:linear-gradient(160deg,#16385a 0%,var(--navy-deep) 100%)}

  /* front */
  .world-map{position:absolute;left:110px;top:40px;width:300px;height:170px;border-radius:40px;
    background:radial-gradient(ellipse at center,rgba(133,172,211,.22) 0%,rgba(133,172,211,0) 70%)}
  .brand{position:absolute;left:30px;top:34px}
  .brand__name{font-weight:900;font-size:40px;letter-spacing:3px;color:var(--navy);line-height:1}
  .brand__tagline{margin-top:4px;font-size:9px;letter-spacing:2.4px;text-transform:uppercase;color:var(--gray)}
  .person{position:absolute;right:30px;top:40px;text-align:right}
  .person__name{font-size:20px;font-weight:300;color:var(--text-gray)}
  .person__name strong{font-weight:700;color:var(--navy)}
  .person__title{font-size:10px;color:var(--text-gray);margin-top:2px}
  .person__rule{position:absolute;right:30px;top:92px;width:150px;height:1px;background:var(--navy)}
  .contact-rule{position:absolute;left:30px;top:160px;width:220px;height:1px;background:var(--navy)}
  .contact{position:absolute;left:30px;top:172px;list-style:none}
  .contact li{display:flex;align-items:center;gap:9px;font-size:13px;color:var(--text-gray);height:21px}
  .contact svg{width:13px;height:13px;fill:var(--navy)}
  .contact__address{font-weight:700;color:var(--brand-blue)}

  /* back */
  .back-brand{position:absolute;left:0;right:0;top:98px;text-align:center;font-weight:900;font-size:46px;letter-spacing:5px;color:#eef1f5}
  .back-url{position:absolute;left:0;right:0;top:210px;text-align:center;font-size:15px;letter-spacing:3px;color:#e6eaef}
</style>
</head>
<body>
  <section class="card card--front" aria-label="Business card front">
    <div class="world-map" role="img" aria-label="Faint dotted world map background"></div>
    <div class="brand">
      <div class="brand__name">TARROW</div>
      <div class="brand__tagline">A Cloud Consulting Company</div>
    </div>
    <div class="person">
      <div class="person__name">Dana <strong>Korvand</strong></div>
      <div class="person__title">Office Manager</div>
    </div>
    <div class="person__rule"></div>
    <div class="contact-rule"></div>
    <ul class="contact">
      <li><svg viewBox="0 0 16 16" aria-hidden="true"><path d="M3 1h3l1.5 4-2 1.5a9 9 0 0 0 4 4L11 8.5l4 1.5v3a2 2 0 0 1-2 2A13 13 0 0 1 1 3a2 2 0 0 1 2-2z"/></svg>555.014.2910</li>
      <li><svg viewBox="0 0 16 16" aria-hidden="true"><path d="M4 1h8v4H4zM1 6h14v6h-3v3H4v-3H1zM5 10v4h6v-4z"/></svg>555.014.2971</li>
      <li><svg viewBox="0 0 16 16" aria-hidden="true"><path d="M1 3h14v10H1zM2 4.2v.6l6 4 6-4v-.6z"/></svg>Dkorvand@Tarrowtech.com</li>
      <li class="contact__address">1180 W Larkin Ave Millbrook Ohio 40112</li>
    </ul>
  </section>

  <section class="card card--back" aria-label="Business card back">
    <div class="back-brand">TARROW</div>
    <div class="back-url">www.Tarrowtech.com</div>
  </section>
</body>
</html>
```